Business Card Design and Logo Needed

I need Business Cards and a Logo for my website and public speaking business which can be found at: www.corvina-lett.example

I'm looking for creative and unique ideas. Some business cards I've found online that I like can be found at:
http://gigbarrow.example/general/18-smokin-hot-business-card-designs/

and at

http://www.plumquarry.example/2009/04/50-creative-business-cards-of-50-graphic-designers/

```html
<!DOCTYPE html>
<html lang="en">
<head>
<meta charset="utf-8">
<title>Corvina Lett — Business Card</title>
<link rel="stylesheet" href="https://fonts.googleapis.com/css2?family=Ubuntu:wght@300;400;700&display=swap">
<style>
  :root {
    --plum: #7b2a7b;
    --plum-faint: #9a5a9b;
    --card-white: #ffffff;
    --backdrop: #ece8e3;
    --card-shadow: rgba(60, 40, 30, 0.22);
  }
  * { margin: 0; padding: 0; box-sizing: border-box; }
  html, body {
    width: 1200px;
    height: 841px;
    overflow: hidden;
    background: var(--backdrop);
    font-family: "Ubuntu", sans-serif;
  }
  .stage { position: relative; width: 1200px; height: 841px; }

  .card {
    position: absolute;
    top: 270px;
    width: 554px;
    height: 278px;
    box-shadow: 3px 4px 8px var(--card-shadow);
  }
  .card--front { left: 34px; background: var(--card-white); color: var(--plum); }
  .card--back { left: 611px; background: var(--plum); }

  .brand-mark {
    position: absolute;
    left: 19px;
    top: 15px;
    width: 80px;
    height: 80px;
  }

  .identity {
    position: absolute;
    left: 96px;
    top: 246px;
    width: 160px;
    transform-origin: left top;
    transform: rotate(-90deg);
    white-space: nowrap;
  }
  .identity__name {
    font-weight: 300;
    font-size: 22px;
    line-height: 26px;
    letter-spacing: 0.3px;
  }
  .identity__role {
    font-weight: 400;
    font-size: 7.5px;
    line-height: 11px;
    margin-left: 2px;
  }

  .contact {
    position: absolute;
    left: 209px;
    top: 88px;
    font-size: 15px;
    line-height: 20px;
    font-weight: 400;
  }
  .contact__group { margin-bottom: 19px; }
  .contact__label, .contact__web { font-weight: 700; }

  .back-mark {
    position: absolute;
    left: 177px;
    top: 49px;
    width: 180px;
    height: 180px;
  }
  .back-mark__name {
    position: absolute;
    left: 0;
    right: 0;
    top: 139px;
    transform: translateY(-50%);
    text-align: center;
    color: var(--plum-faint);
    font-weight: 300;
    font-size: 18px;
  }
</style>
</head>
<body>
<main class="stage">
  <section class="card card--front" aria-label="Business card front">
    <svg class="brand-mark" viewBox="0 0 80 80" aria-hidden="true">
      <circle cx="40" cy="40" r="38" fill="none" stroke="var(--plum)" stroke-width="2"/>
    </svg>
    <div class="identity">
      <p class="identity__name">Corvina Lett</p>
      <p class="identity__role">Public Speaker &amp; Philanthropist</p>
    </div>
    <div class="contact">
      <p class="contact__group">2210 Marlowe Row, Suite 400<br>Ashvale, Texas 77990</p>
      <p class="contact__group">
        <span class="contact__label">Phone</span> 555 014 2287<br>
        <span class="contact__label">Fax</span> 555 019 6630<br>
        <span class="contact__label">Email</span> info@corvinalett.example
      </p>
      <p class="contact__web">www.corvina-lett.example</p>
    </div>
  </section>

  <section class="card card--back" aria-label="Business card back">
    <svg class="back-mark" viewBox="0 0 180 180" aria-hidden="true">
      <circle cx="90" cy="90" r="82" fill="none" stroke="var(--plum-faint)" stroke-width="1.5"/>
    </svg>
    <p class="back-mark__name">Corvina Lett</p>
  </section>
</main>
</body>
</html>
```